Mental Health Therapy Website

I need a design for a mental health therapy website. It is a private practice. The business name is Fenwick Counseling, PLLC. My name is Martin Fenwick, LMHC, NCC, DCC. I would like some of the features/menus to be Home; Welcome/About Me, Rates and Services, Common Questions, and Contact.
If possible I would like a blog on the main page that I can update with articles I write. I would like the contact page to feature a map to my location (4189 Birchmont Ave. S, Lakewood, WA 98312).
I would like to place a small photo of me on the Welcome/About page.
I am new to this so if I am forgetting anything, please ask me!!
I will upload my logo so you can fit it and the color scheme into the design.
Thank you so very much!

```html
<!DOCTYPE html>
<html lang="en">
<head>
<meta charset="utf-8">
<title>Fenwick Counseling, PLLC</title>
<link href="https://fonts.googleapis.com/css2?family=Source+Sans+3:wght@300;400;600;700&display=swap" rel="stylesheet">
<style>
  :root {
    --brand-blue: #2a92cb;
    --brand-blue-dark: #1f7fb6;
    --logo-blue: #2c6f9e;
    --ink: #3a3a3a;
    --body-text: #555555;
    --nav-text: #4a4a4a;
    --rule: #e3e6e8;
    --white: #ffffff;
    --hero-top: #9cc4da;
    --hero-bottom: #6ea6c6;
    --stripe-1: #e94b8a;
    --stripe-2: #f5a623;
    --stripe-3: #f8e13c;
    --stripe-4: #7cc242;
    --stripe-5: #2fb5c8;
    --stripe-6: #3b6fc4;
    --stripe-7: #8c5ac8;
  }
  * { margin: 0; padding: 0; box-sizing: border-box; }
  html, body {
    width: 1200px; height: 1111px; overflow: hidden;
    background: var(--white);
    font-family: "Source Sans 3", "Source Sans Pro", Arial, sans-serif;
    color: var(--ink);
  }
  .page { position: relative; width: 1200px; height: 1111px; }

  .color-stripe {
    position: absolute; left: 0; width: 1200px; height: 4px;
    background: linear-gradient(90deg,
      var(--stripe-1) 0 14%, var(--stripe-2) 14% 28%, var(--stripe-3) 28% 42%,
      var(--stripe-4) 42% 57%, var(--stripe-5) 57% 71%, var(--stripe-6) 71% 85%,
      var(--stripe-7) 85% 100%);
  }
  .color-stripe.top { top: 0; }
  .color-stripe.bottom { top: 1058px; }

  .site-header {
    position: absolute; top: 4px; left: 0; width: 1200px; height: 72px;
    border-bottom: 2px solid var(--rule);
  }
  .brand {
    position: absolute; left: 96px; top: 14px;
    display: flex; align-items: center; gap: 10px;
  }
  .brand-dot {
    width: 40px; height: 40px; border-radius: 50%;
    background: var(--logo-blue);
  }
  .brand-name {
    font-size: 26px; font-weight: 600; color: var(--logo-blue);
    line-height: 1; letter-spacing: 0.2px;
  }
  .main-nav { position: absolute; top: 21px; left: 0; }
  .main-nav a {
    position: absolute; top: 0; height: 32px; line-height: 32px;
    font-size: 11px; text-transform: uppercase; text-decoration: none;
    color: var(--nav-text); white-space: nowrap; letter-spacing: 0.2px;
  }
  .main-nav a.active {
    background: var(--brand-blue); color: var(--white);
    border-radius: 3px; width: 68px; text-align: center;
  }

  .hero {
    position: absolute; top: 78px; left: 0; width: 1200px; height: 278px;
  }
  .hero-photo {
    position: absolute; inset: 0;
    background: linear-gradient(160deg, var(--hero-top) 0%, #86b5cf 50%, var(--hero-bottom) 100%);
  }
  .hero-text { position: absolute; inset: 0; text-align: center; color: var(--white); }
  .hero-title {
    position: absolute; top: 100px; width: 100%;
    font-size: 42px; font-weight: 700; letter-spacing: 0.5px;
  }
  .hero-subtitle {
    position: absolute; top: 150px; width: 100%;
    font-size: 23px; font-weight: 400;
  }

  .features {
    position: absolute; top: 356px; left: 0; width: 1200px; height: 285px;
    display: flex;
  }
  .feature { position: relative; height: 100%; text-align: center; }
  .feature.blue { background: var(--brand-blue); color: var(--white); }
  .feature.plain { background: var(--white); color: var(--ink); }
  .feature-icon { position: absolute; top: 42px; left: 50%; transform: translateX(-50%); }
  .feature-title {
    position: absolute; top: 92px; width: 100%;
    font-size: 25px; font-weight: 600; text-transform: uppercase; letter-spacing: 0.3px;
  }
  .feature-text {
    position: absolute; top: 133px; left: 22px; right: 22px;
    font-size: 14.5px; line-height: 22px;
  }
  .feature.plain .feature-text { top: 133px; left: 18px; right: 18px; font-size: 13.5px; line-height: 21.5px; color: var(--ink); }
  .appointment-button {
    position: absolute; top: 214px; left: 116px; width: 167px; height: 31px;
    background: var(--brand-blue); color: var(--white); border-radius: 2px;
    font-size: 10.5px; line-height: 31px; text-transform: uppercase; text-decoration: none;
  }

  .intro-section { position: absolute; top: 690px; left: 94px; width: 1014px; }
  .section-heading {
    font-size: 27px; font-weight: 300; color: var(--brand-blue);
    text-transform: uppercase; letter-spacing: 0.2px;
    padding-bottom: 6px; border-bottom: 3px solid #f0f2f3;
  }
  .section-heading strong { font-weight: 700; }
  .intro-copy { position: absolute; top: 72px; left: 0; width: 630px; }
  .intro-copy p {
    font-size: 14.5px; line-height: 27px; color: var(--body-text); margin-bottom: 17px;
  }
  .intro-photo {
    position: absolute; top: 70px; left: 658px; width: 356px; height: 236px;
    border-radius: 3px;
    background: linear-gradient(120deg, #e9dcc0 0%, #d8c59f 45%, #4fb3ad 75%, #c9b58f 100%);
  }
</style>
</head>
<body>
<div class="page">
  <div class="color-stripe top"></div>

  <header class="site-header">
    <div class="brand">
      <span class="brand-dot"></span>
      <span class="brand-name">Fenwick Counseling</span>
    </div>
    <nav class="main-nav">
      <a class="active" href="#" style="left:555px;">Home</a>
      <a href="#" style="left:644px;">About Me</a>
      <a href="#" style="left:738px;">Rates and Services</a>
      <a href="#" style="left:887px;">Common Questions</a>
      <a href="#" style="left:1039px;">Contact</a>
    </nav>
  </header>

  <section class="hero">
    <div class="hero-photo" role="img" aria-label="Photo of a hand touching a medical monitor screen, tinted blue"></div>
    <div class="hero-text">
      <h1 class="hero-title">HERE IS MARTIN FENWICK</h1>
      <p class="hero-subtitle">I am a trauma certified therapist that utilizes CBT+ to assist with trauma</p>
    </div>
  </section>

  <section class="features">
    <div class="feature blue" style="width:401px;">
      <svg class="feature-icon" width="24" height="34" viewBox="0 0 24 34" aria-hidden="true">
        <path d="M12 1 C12 1 1 16 1 22 A11 11 0 0 0 23 22 C23 16 12 1 12 1 Z" fill="#ffffff"/>
        <path d="M6 22 A6 6 0 0 0 11 28" stroke="#2a92cb" stroke-width="2" fill="none"/>
      </svg>
      <h2 class="feature-title">Psychoeducation</h2>
      <p class="feature-text">Lorem ipsum dolor sit amet, consectetuer adipiscing elit, sed diam nonummy nibh euismod tincidunt ut laoreet dolore magna aliquam erat volutpat. Ut wisi enim ad minim veniam, quis nostrud exerci tation.</p>
    </div>
    <div class="feature plain" style="width:400px;">
      <svg class="feature-icon" width="34" height="34" viewBox="0 0 34 34" aria-hidden="true" style="top:44px;">
        <circle cx="17" cy="17" r="14.5" fill="none" stroke="#3a3a3a" stroke-width="3.5"/>
        <path d="M17 9 V18 H24" fill="none" stroke="#3a3a3a" stroke-width="3"/>
      </svg>
      <h2 class="feature-title">Ask for Session</h2>
      <p class="feature-text">If you need a doctor for to consectetuer Lorem ipsum dolor, consectetur adipiscing elit. Ut volutpat eros s adipiscing elit. Ut volutpat eros sit.</p>
      <a class="appointment-button" href="#">Make an Appointment</a>
    </div>
    <div class="feature blue" style="width:399px;">
      <svg class="feature-icon" width="24" height="34" viewBox="0 0 24 34" aria-hidden="true">
        <path d="M12 1 C12 1 1 16 1 22 A11 11 0 0 0 23 22 C23 16 12 1 12 1 Z" fill="#ffffff"/>
        <path d="M6 22 A6 6 0 0 0 11 28" stroke="#2a92cb" stroke-width="2" fill="none"/>
      </svg>
      <h2 class="feature-title">Therapy by CBT Tools</h2>
      <p class="feature-text">Lorem ipsum dolor sit amet, consectetuer adipiscing elit, sed diam nonummy nibh euismod tincidunt ut laoreet dolore magna aliquam erat volutpat. Ut wisi enim ad minim veniam, quis nostrud exerci tation.</p>
    </div>
  </section>

  <section class="intro-section">
    <h2 class="section-heading">Mental Health <strong>Counselling/Therapy</strong></h2>
    <div class="intro-copy">
      <p>Etharums ser quidem rerum facilis dolores nemis omnis fugats vitaes nemo minima rerums unsers sadips amets. Sed ut perspiciatis unde omnis iste natus error sit voluptatem accusantium doloremque laudantium, totam rem aperiam, eaque ipsa quae ab illo inventore.</p>
      <p>veritatis et quasi architecto beatae vitae dicta sunt explicabo. Nemo enim ipsam voluptatem quia voluptas sit aspernatur aut odit aut fugit, sed quia consequuntur magni dolores eos qui ratione voluptatem sequi nesciunt.</p>
      <p>Sed ut perspiciatis unde omnis iste natus error sit voluptatem accusantium doloremque laudantium, totam rem aperiam, eaque ipsa quae ab illo inventore.</p>
    </div>
    <div class="intro-photo" role="img" aria-label="Photo of a counselor taking notes while talking with a mother and daughter seated on a sofa"></div>
  </section>

  <div class="color-stripe bottom"></div>
</div>
</body>
</html>
```